Powerpoint and Word template required

We need PowerPoint and Word templates for all of our company branded materials and stationary. We have recently rebranded our website and would like something that is reflective of our new corporate branding. A sample of some of the documents we have created recently are attached and our website is below

http://lorwynmedical.com.au/

The word template will be used for all letters we send to clients and customers and we think we want the logo and ISO 9001 cert to only appear on the first page.

The powerpoint template has to be flexible as we use this for both marketing and training purposes. I have attached a couple of samples of the types of documents we create and note that these are very basic / crude and we would be looking for something that is a significant improvement on these

In the powerpoint template it would be good to have lots of standard layouts within the template, e.g. different 'standard layouts for multiple elements on a page including pictures and text etc.
Updates

Project Deadline Extended
Reason: Still looking for a professional yet modern template and important to us that we can see more tan just a title slide and the layout of the other slide master slides is very important to us. Many thanks, Dale

Industry/Entity Type

Healthcare

Font styles to use
Sans Serif

Colors
33a6d7

Requirements
Must have
• Templates must be versatile for use; powerpoint template must be able to be used for training materials and weel as marketing / pitch books.
• Word template must be able to be used as a basis for our corporate letter head through to RFP response type documents as well as Reference / Operating manual type of documents
• In terms of the design it must be consistent with our new corporate image which is best represented by our new website design; www.lorwynmedical.com

```html
<!DOCTYPE html>
<html lang="en">
<head>
<meta charset="utf-8">
<title>Lorwyn Presentation Template</title>
<link rel="stylesheet" href="https://fonts.googleapis.com/css2?family=Oswald:wght@400;500&family=Roboto+Condensed:wght@400;700&display=swap">
<style>
:root{
  --blue:#2b82cf;
  --blue-dark:#1f6cb5;
  --accent:#33a6d7;
  --ink:#3a3a3a;
  --muted:#7d8791;
  --slide-bg:#e9f0f7;
  --teal:#3cc6b4;
  --black:#000;
}
*{box-sizing:border-box;margin:0;padding:0}
html,body{width:1200px;height:1200px;overflow:hidden;background:var(--black)}
body{font-family:"Roboto Condensed",Arial,sans-serif;color:var(--ink)}
.sheet{width:1200px;height:1200px;display:grid;grid-template-columns:repeat(3,374px);grid-template-rows:repeat(4,280px);gap:12px;padding:22px 27px}
.slide{position:relative;overflow:hidden;background:linear-gradient(180deg,#f3f7fb 0%,var(--slide-bg) 70%,#dfe8f2 100%)}
.slide-title{position:absolute;left:7px;top:9px;font-family:"Oswald",sans-serif;font-size:10.5px;color:var(--blue);letter-spacing:.2px;border-bottom:1px solid var(--blue);padding-bottom:1px;text-transform:uppercase}
.brand{position:absolute;right:8px;top:7px;display:flex;align-items:center;gap:4px}
.brand-mark{width:12px;height:12px;background:var(--blue)}
.brand-name{font-family:"Oswald",sans-serif;font-weight:500;font-size:14px;color:var(--blue);line-height:1}
.footer-tag{position:absolute;left:0;bottom:5px;background:var(--blue);color:#fff;font-size:6.5px;padding:3px 5px}
.footer-url{position:absolute;left:0;right:0;bottom:7px;text-align:center;font-size:6px;color:var(--muted)}
.page-no{position:absolute;right:6px;bottom:5px;background:#222;color:#fff;font-size:6px;padding:2px 3px}
.photo{position:absolute}
.icon-sq{display:inline-block;width:10px;height:10px;background:var(--blue);margin-right:6px;vertical-align:-1px;position:relative}
.icon-sq::after{content:"";position:absolute;left:3px;top:2px;width:4px;height:4px;border:1px solid #fff}

/* title slide */
.s-title .photo{left:0;top:0;width:374px;height:174px;background:linear-gradient(120deg,#c9d6e2,#eef3f8 45%,#9fc3e6 85%)}
.s-title .client{position:absolute;left:18px;top:200px;font-family:"Oswald",sans-serif;font-size:12px;color:var(--blue)}
.s-title .sub{position:absolute;left:18px;top:220px;font-size:7px;color:var(--muted)}
.s-title .date{position:absolute;left:18px;top:239px;font-size:7.5px;color:var(--muted)}
.s-title .brand{top:210px;right:18px}
.s-title .brand-mark{width:28px;height:28px}
.s-title .brand-name{font-size:32px}
.s-title .band{position:absolute;left:0;right:0;bottom:0;height:9px;background:var(--blue)}

/* checklist */
.checklist{position:absolute;top:45px;font-family:"Oswald",sans-serif;font-size:8.3px;color:var(--ink);list-style:none}
.checklist li{height:20.5px}
.checklist.left{left:20px}.checklist.right{left:202px}

/* products */
.products{position:absolute;left:0;right:0;top:80px;display:flex;justify-content:space-around;padding:0 10px}
.product{width:110px;text-align:center}
.product .ring{position:relative;width:76px;height:76px;margin:0 auto;border-radius:50%;border:3px solid var(--blue);background:linear-gradient(160deg,#b9a27c,#6c6f74 60%,#d8dde3)}
.product .tick{position:absolute;right:-6px;top:-2px;width:24px;height:24px}
.product h3{font-family:"Oswald",sans-serif;font-weight:400;font-size:8.5px;color:var(--blue);margin-top:10px}
.product p{font-size:6.3px;line-height:1.5;margin-top:2px}

/* about */
.about h3{position:absolute;left:18px;top:55px;font-family:"Oswald",sans-serif;font-weight:400;font-size:8.5px;color:var(--blue)}
.about .copy{position:absolute;left:18px;top:70px;width:140px;font-size:6.3px;line-height:1.8}
.about .copy p{margin-bottom:7px}
.about .photo{left:164px;top:60px;width:210px;height:108px;background:linear-gradient(150deg,#2e3e7a,#4a5c9c 60%,#c9c7bd)}
.about .quote{position:absolute;left:164px;top:160px;width:210px;height:76px;background:var(--blue);color:#fff;font-style:italic;font-size:7.5px;line-height:1.6;padding:12px 12px}

/* solutions */
.solutions{position:absolute;left:0;right:0;top:36px;display:grid;grid-template-columns:repeat(3,1fr);gap:2px;height:216px}
.sol{display:flex;flex-direction:column}
.sol h3{background:var(--blue);color:#fff;font-family:"Oswald",sans-serif;font-weight:500;font-size:10.5px;text-align:center;padding:8px 0 6px}
.sol .photo{position:static;height:110px}
.sol p{flex:1;background:var(--blue);color:#fff;font-size:7px;line-height:1.5;text-align:center;padding:8px 5px}

/* rental */
.rental .intro{position:absolute;left:12px;top:44px;width:352px;font-size:6px;line-height:1.9}
.rental .intro b{color:var(--blue);font-weight:400;font-size:7px}
.rental h3{position:absolute;left:12px;top:123px;font-family:"Roboto Condensed",sans-serif;font-weight:400;font-size:7.5px;color:var(--blue)}
.rental ul{position:absolute;left:20px;top:140px;list-style:none;font-size:6.5px}
.rental li{height:21.5px}

/* constant low pressure */
.clp .panel{position:absolute;left:0;top:37px;width:167px;height:211px;background:var(--blue)}
.clp ul{position:absolute;left:10px;top:60px;list-style:none;font-family:"Oswald",sans-serif;font-size:8.3px;color:#fff}
.clp li{margin-bottom:14px;line-height:1.5}
.clp li .icon-sq{background:transparent;border:1px solid #fff}
.clp .photo{left:167px;top:37px;width:207px;height:211px;background:linear-gradient(170deg,#8e7d90 0%,#5a4a5e 25%,#efefd9 40%,#e6edc5 55%,#a8d6c2 72%,#7d7f84 90%)}

.overlay .field{position:absolute;left:0;top:37px;width:374px;height:211px;background:linear-gradient(135deg,#3c8bd3,var(--blue) 60%,#5a9dd8)}
.overlay .heading{position:absolute;left:8px;top:128px;font-family:"Oswald",sans-serif;font-size:14px;color:#fff}
.overlay .photo{left:236px;top:84px;width:120px;height:120px;border:2px solid #8fc2ec;background:linear-gradient(160deg,#bcc6cf,#8f9ba6 50%,#3d6fc0)}

/* control panel */
.control .photo.panel-photo{left:0;top:37px;width:374px;height:138px;background:linear-gradient(180deg,#dfe5ea,#c5d0d8)}
.control .specs{position:absolute;left:20px;top:186px;font-size:9.5px;line-height:1.95}
.control .specs dt{float:left;clear:left;width:100px;font-family:"Oswald",sans-serif;color:var(--blue)}
.control .specs dd{margin-left:100px;font-family:"Oswald",sans-serif;color:#222}
.control .specs dd::before{content:":  "}
.control2 .photo.panel-photo{height:128px}
.control2 .dots{position:absolute;left:14px;top:133px;display:flex;gap:31px}
.control2 .dot{width:63px;height:63px;border-radius:50%;border:2px solid var(--blue)}
.control2 .specs{top:202px;left:16px;font-size:8.5px;line-height:1.85}
.control2 .specs dt{width:94px}
.control2 .specs dd{margin-left:94px}

.divider .field{position:absolute;left:0;top:30px;width:374px;height:222px;background:var(--blue)}
.divider .heading{position:absolute;left:0;right:0;top:128px;text-align:center;font-family:"Oswald",sans-serif;font-weight:500;font-size:22px;color:#fff;letter-spacing:.5px}

.thanks{background:var(--blue)}
.thanks h2{position:absolute;left:0;right:0;top:48px;text-align:center;font-family:"Oswald",sans-serif;font-weight:500;font-size:22px;color:#fff;letter-spacing:.5px}
.thanks .brand{left:0;right:0;top:95px;justify-content:center}
.thanks .brand-mark{width:22px;height:22px;background:#fff}
.thanks .brand-name{color:#fff;font-size:26px}
.thanks .offices{position:absolute;left:0;right:0;top:148px;display:flex;justify-content:center;gap:30px;color:#fff;font-size:6.3px;line-height:2}
.thanks .offices h4{font-family:"Oswald",sans-serif;font-weight:400;font-size:8px}
.thanks .office-left{text-align:right}
.thanks .note{position:absolute;left:0;right:0;top:212px;text-align:center;color:#fff;font-size:7px;line-height:1.8}
.thanks .footer-url{color:#c7def3}
</style>
</head>
<body>
<main class="sheet">

  <section class="slide s-title">
    <div class="photo" role="img" aria-label="Photo of a doctor with patients in a hospital ward"></div>
    <h1 class="client">EASTBROOK HEALTH</h1>
    <p class="sub">REVIEW OF PRESSURE INJURY PREVENTION EQUIPMENT</p>
    <p class="date">MARCH-2016</p>
    <div class="brand"><span class="brand-mark"></span><span class="brand-name">Lorwyn</span></div>
    <div class="band"></div>
  </section>

  <section class="slide">
    <h2 class="slide-title">Issues to consider when prescribing an APAM</h2>
    <div class="brand"><span class="brand-mark"></span><span class="brand-name">Lorwyn</span></div>
    <ul class="checklist left">
      <li><span class="icon-sq"></span>DEGREE OF BED MOBILITY.</li>
      <li><span class="icon-sq"></span>WEIGHT OF PATIENT.</li>
      <li><span class="icon-sq"></span>SENSATION</li>
      <li><span class="icon-sq"></span>LOCATION OF PRESSURE ULCER.</li>
      <li><span class="icon-sq"></span>STAGE OF PRESSURE INJURY.</li>
      <li><span class="icon-sq"></span>EVALUATION OF RISK ASSESSMENT</li>
      <li><span class="icon-sq"></span>CONTINUOUS EVALUATION</li>
      <li><span class="icon-sq"></span>PREVIOUS HISTORY</li>
      <li><span class="icon-sq"></span>SKIN INTEGRITY</li>
    </ul>
    <ul class="checklist right">
      <li><span class="icon-sq"></span>DEGREE OF BED MOBILITY.</li>
      <li><span class="icon-sq"></span>WEIGHT OF PATIENT.</li>
      <li><span class="icon-sq"></span>SENSATION</li>
      <li><span class="icon-sq"></span>LOCATION OF PRESSURE ULCER.</li>
      <li><span class="icon-sq"></span>STAGE OF PRESSURE INJURY.</li>
      <li><span class="icon-sq"></span>EVALUATION OF RISK ASSESSMENT</li>
      <li><span class="icon-sq"></span>CONTINUOUS EVALUATION</li>
      <li><span class="icon-sq"></span>PREVIOUS HISTORY</li>
      <li><span class="icon-sq"></span>SKIN INTEGRITY</li>
    </ul>
    <span class="footer-tag">Copyright text here</span><p class="footer-url">||&nbsp; www.lorwynmedical.com.au &nbsp;||</p><span class="page-no">01</span>
  </section>

  <section class="slide">
    <h2 class="slide-title">Product Section</h2>
    <div class="brand"><span class="brand-mark"></span><span class="brand-name">Lorwyn</span></div>
    <div class="products">
      <div class="product"><div class="ring" role="img" aria-label="Product photo of a mattress overlay"><svg class="tick" viewBox="0 0 24 24"><circle cx="12" cy="12" r="11" fill="#2b82cf" stroke="#fff" stroke-width="1.5"/><path d="M6.5 12.5l3.5 3.5 7-7.5" fill="none" stroke="#fff" stroke-width="2.4"/></svg></div><h3>Product Title Here</h3><p>Skin whitens under compression due to local occlusion or vasoconstriction of the blood supply.</p></div>
      <div class="product"><div class="ring" role="img" aria-label="Product photo of a mattress overlay"><svg class="tick" viewBox="0 0 24 24"><circle cx="12" cy="12" r="11" fill="#2b82cf" stroke="#fff" stroke-width="1.5"/><path d="M6.5 12.5l3.5 3.5 7-7.5" fill="none" stroke="#fff" stroke-width="2.4"/></svg></div><h3>Product Title Here</h3><p>Skin whitens under compression due to local occlusion or vasoconstriction of the blood supply.</p></div>
      <div class="product"><div class="ring" role="img" aria-label="Product photo of a mattress overlay"><svg class="tick" viewBox="0 0 24 24"><circle cx="12" cy="12" r="11" fill="#2b82cf" stroke="#fff" stroke-width="1.5"/><path d="M6.5 12.5l3.5 3.5 7-7.5" fill="none" stroke="#fff" stroke-width="2.4"/></svg></div><h3>Product Title Here</h3><p>Skin whitens under compression due to local occlusion or vasoconstriction of the blood supply.</p></div>
    </div>
    <span class="footer-tag">Copyright text here</span><p class="footer-url">||&nbsp; www.lorwynmedical.com.au &nbsp;||</p><span class="page-no">01</span>
  </section>

  <section class="slide about">
    <h2 class="slide-title">About Us</h2>
    <div class="brand"><span class="brand-mark"></span><span class="brand-name">Lorwyn</span></div>
    <h3>Patient Centred Care</h3>
    <div class="copy">
      <p>Lorwyn Healthcare is the leading supplier of high quality, clinically proven products for the prevention and management of pressure ulcers in the acute, community and residential care sectors.</p>
      <p>Our clinically proven products are supported by a portfolio of quality assured services such as 24/7 rental service, expert training and education, equipment management solutions as well as service and maintenance programs.</p>
      <p>Lorwyn Healthcare guarantees a first class level of service that will enable you to provide the world's best practice in pressure area care.</p>
    </div>
    <div class="photo" role="img" aria-label="Photo of an air mattress with its control pump"></div>
    <p class="quote">"Clinically proven solutions to enhance pressure care excellence Clinically proven solutions to enhance pressure care excellence Clinically proven solutions to enhance pressure"</p>
    <span class="footer-tag">Copyright text here</span><p class="footer-url">||&nbsp; www.lorwynmedical.com.au &nbsp;||</p><span class="page-no">01</span>
  </section>

  <section class="slide">
    <h2 class="slide-title">Our Solutions</h2>
    <div class="brand"><span class="brand-mark"></span><span class="brand-name">Lorwyn</span></div>
    <div class="solutions">
      <div class="sol"><h3>BLANCHING</h3><div class="photo" role="img" aria-label="Clinical photo of heels showing blanched skin" style="background:linear-gradient(180deg,#6a6a6a,#c9bdb4 55%,#4a4a4a)"></div><p>Skin whitens under compression due to local occlusion or vasoconstriction of the blood supply.</p></div>
      <div class="sol"><h3>BLANCHING</h3><div class="photo" role="img" aria-label="Clinical close-up of reddened skin" style="background:linear-gradient(150deg,#e8b2a8,#c44b4f 55%,#e3a49a)"></div><p>Courtesy of J. Rowe<br>After prolonged and unrelieved pressure we get 'Reactive Hyperaemia'</p></div>
      <div class="sol"><h3>BLANCHING ERYTHEMA?</h3><div class="photo" role="img" aria-label="Clinical photo of skin erythema beside a measuring ruler" style="background:linear-gradient(180deg,#e9ece9 0 30%,#d9a39b 55%,#c77d7a)"></div><p>Intact microcirculation is indicated when reddened skin – 'Erythema' - blanches or whitens, after light finger pressure is applied.</p></div>
    </div>
    <span class="footer-tag">Copyright text here</span><p class="footer-url">||&nbsp; www.lorwynmedical.com.au &nbsp;||</p><span class="page-no">01</span>
  </section>

  <section class="slide rental">
    <h2 class="slide-title">Equipment Rental</h2>
    <div class="brand"><span class="brand-mark"></span><span class="brand-name">Lorwyn</span></div>
    <p class="intro"><b>Lorwyn Healthcare</b> has been a leading supplier of rental equipment to Australian Health Care Facilities and to people living in the community since 1990. Through our program of continuing product and service improvement we offer an unsurpassed, quality assured rental service that enables clinicians to offer the world's best practice in pressure injury care. We understand that the care environment rapidly changes and that your product requirements to optimise patient care will change. Access to our innovative range of pressure area care mattresses, specialist bariatric products or durable medical equipment on a rental basis will allow you to cope with the varying operational demands being placed on you.</p>
    <h3>Features of Equipment Rental with Lorwyn Healthcare</h3>
    <ul>
      <li><span class="icon-sq"></span>Access to an extensive portfolio of clinically proven products.</li>
      <li><span class="icon-sq"></span>Effortless online ordering, cancelation and transfer of equipment through KitTrack Online.</li>
      <li><span class="icon-sq"></span>Complete cleaning and decontamination services in accordance with national cleaning guidelines.</li>
      <li><span class="icon-sq"></span>Real-time equipment tracking through our KitTrack Online.</li>
      <li><span class="icon-sq"></span>24-hour Customer Services Helpline.</li>
    </ul>
    <span class="footer-tag">Copyright text here</span><p class="footer-url">||&nbsp; www.lorwynmedical.com.au &nbsp;||</p><span class="page-no">01</span>
  </section>

  <section class="slide clp">
    <h2 class="slide-title">Constant Low Pressure</h2>
    <div class="brand"><span class="brand-mark"></span><span class="brand-name">Lorwyn</span></div>
    <div class="panel"></div>
    <ul>
      <li><span class="icon-sq"></span>HIGH SPECIFICATION FOAMS</li>
      <li><span class="icon-sq"></span>STRETCH COVER</li>
      <li><span class="icon-sq"></span>MULTI LAYERS OF DIFFERENT<br>DENSITY FOAMS</li>
    </ul>
    <div class="photo" role="img" aria-label="Cutaway photo of a layered foam mattress with stretch cover"></div>
    <span class="footer-tag">Copyright text here</span><p class="footer-url">||&nbsp; www.lorwynmedical.com.au &nbsp;||</p><span class="page-no">01</span>
  </section>

  <section class="slide overlay">
    <h2 class="slide-title">Constant Low Pressure</h2>
    <div class="brand"><span class="brand-mark"></span><span class="brand-name">Lorwyn</span></div>
    <div class="field" role="img" aria-label="Faded blue-tinted photo of a hospital bed"></div>
    <p class="heading">INSIDE LOOK AT A LORWYN OVERLAY</p>
    <div class="photo" role="img" aria-label="Photo of the air cells inside a mattress overlay"></div>
    <span class="footer-tag">Copyright text here</span><p class="footer-url">||&nbsp; www.lorwynmedical.com.au &nbsp;||</p><span class="page-no">01</span>
  </section>

  <section class="slide control">
    <h2 class="slide-title">Control Panel</h2>
    <div class="brand"><span class="brand-mark"></span><span class="brand-name">Lorwyn</span></div>
    <div class="photo panel-photo" role="img" aria-label="Photo of the pump control panel with mode, program, max inflation, reset alarm and deflate buttons"></div>
    <dl class="specs">
      <dt>MODE BUTTON</dt><dd>Dynamic to Static mode.&nbsp; Static 30 minutes only</dd>
      <dt>PROGRAM BUTTON</dt><dd>Low, Normal &amp; High Pressure setting</dd>
      <dt>MAX INFLATE</dt><dd>For bed side procedures.&nbsp; Max Time 20 Minutes</dd>
    </dl>
    <span class="footer-tag">Copyright text here</span><p class="footer-url">||&nbsp; www.lorwynmedical.com.au &nbsp;||</p><span class="page-no">01</span>
  </section>

  <section class="slide control control2">
    <h2 class="slide-title">Control Panel</h2>
    <div class="brand"><span class="brand-mark"></span><span class="brand-name">Lorwyn</span></div>
    <div class="photo panel-photo" role="img" aria-label="Photo of the pump control panel buttons"></div>
    <div class="dots">
      <div class="dot" role="img" aria-label="Close-up of a hand pressing the mode button" style="background:linear-gradient(140deg,#c9a07f,#5c5f66)"></div>
      <div class="dot" role="img" aria-label="Close-up of the pump unit label" style="background:linear-gradient(160deg,#e8e6dc,#b8b8ae)"></div>
      <div class="dot" role="img" aria-label="Close-up of a red release valve" style="background:radial-gradient(circle,#e8302b 40%,#b8b0a8 70%)"></div>
      <div class="dot" role="img" aria-label="Close-up of the pump digital display" style="background:linear-gradient(160deg,#dfe3ea,#6f8bb9)"></div>
    </div>
    <dl class="specs">
      <dt>MODE BUTTON</dt><dd>Dynamic to Static mode.&nbsp; Static 30 minutes only</dd>
      <dt>PROGRAM BUTTON</dt><dd>Low, Normal &amp; High Pressure setting</dd>
      <dt>MAX INFLATE</dt><dd>For bed side procedures.&nbsp; Max Time 20 Minutes</dd>
    </dl>
    <span class="footer-tag">Copyright text here</span><p class="footer-url">||&nbsp; www.lorwynmedical.com.au &nbsp;||</p><span class="page-no">01</span>
  </section>

  <section class="slide divider">
    <div class="brand"><span class="brand-mark"></span><span class="brand-name">Lorwyn</span></div>
    <div class="field"></div>
    <h2 class="heading">SECTION DIVIDER HERE</h2>
    <span class="footer-tag">Copyright text here</span><p class="footer-url">||&nbsp; www.lorwynmedical.com.au &nbsp;||</p><span class="page-no">01</span>
  </section>

  <section class="slide thanks">
    <h2>THANKS FOR YOUR TIME</h2>
    <div class="brand"><span class="brand-mark"></span><span class="brand-name">Lorwyn</span></div>
    <div class="offices">
      <div class="office-left"><h4>HEAD OFFICE LOCATIONS</h4><p><b>Sydney</b> : Lorwyn Healthcare (NSW)</p><p>12/48 Carrow Street, Ashgrove, NSW 2170</p><p>Ph: (02) 9000 4812</p></div>
      <div><h4>BRANCH OFFICE LOCATIONS</h4><p><b>Melbourne</b> : Lorwyn Healthcare (Vic)</p><p>215 Harlow Road, Elmvale, VIC 3187</p><p>Ph: (03) 9000 2735</p></div>
    </div>
    <p class="note"><b>Our Service Centres are located throughout Australia.<br>To find your nearest Service Centre please call 1300 000 418</b></p>
    <span class="footer-tag">Copyright text here</span><p class="footer-url">||&nbsp; www.lorwynmedical.com.au &nbsp;||</p><span class="page-no">01</span>
  </section>

</main>
</body>
</html>
```